Professional Website for Leading Global Private Equity Real Estate Company

The company is a leading global Private Equity Real Estate (PERE). We need a homepage design, an inner page design, and color/font tweaks to the logo (color should be more soothing than current blue used in the logo). The logo website should project the company as global, professional, experienced, trustworthy, accessible, YOUNG, DYNAMIC, hi-tech. PLEASE SEE the attached Design Brief Word Doc for details.

Target Market(s)

institional investors and wealthy private individuals

Industry/Entity Type

Finance

Number of Pages Required

2 page

Font styles to use
Sans Serif
Other font styles liked:
• either like in https://www.ferndalequay.com/ or like in presentations (Montserrat Black & Montserrat Light, Century Gothic, Blair ITC, Almoni Neue DL 4.0 AAA Medium, Almoni DL AAA)

Requirements
Must have
• new color palette that is NOT based on current logo. they want a more soothing color palette than the blue in that logo. the new color palette should project: global, professional, experienced, trustworthy, accessible, YOUNG, DYNAMIC, hi-tech.
Nice to have
• the likes these sites: https://www.ferndalequay.com/ and https://www.tvr.law/

```html
<!DOCTYPE html>
<html lang="en">
<head>
<meta charset="utf-8">
<title>Veyra Real Estate – Homepage Concepts</title>
<link href="https://fonts.googleapis.com/css2?family=Montserrat:wght@300;400;500;600;700;800&display=swap" rel="stylesheet">
<style>
:root{
  --stage:#d7d7d7;
  --ink:#1d2b45;
  --body:#5a6270;
  --muted:#8a919c;
  --line:#d9dde2;
  --green:#2f8f74;
  --green-dark:#236f5a;
  --purple:#6a3d9b;
  --purple-light:#9a6ad8;
  --cyan:#1cc6bd;
  --teal:#1f878b;
  --teal-dark:#1b5f66;
  --navy:#1f3b8a;
  --grey-band:#eeeeee;
  --white:#ffffff;
}
*{box-sizing:border-box;margin:0;padding:0}
html,body{width:1200px;height:1200px;overflow:hidden}
body{background:var(--stage);font-family:"Montserrat",Arial,sans-serif;color:var(--ink);position:relative}
.page{position:absolute;top:34px;background:var(--white);overflow:hidden;display:flex;flex-direction:column}
.page--green{left:73px;width:300px}
.page--purple{left:406px;width:318px}
.page--teal{left:760px;width:322px}
section,footer,header{position:relative;flex:none;overflow:hidden}
.abs{position:absolute}
.img{position:absolute}
/* nav */
.nav{position:absolute;top:0;left:0;right:0;height:24px;display:flex;align-items:center;padding:0 0 0 24px;color:var(--white);z-index:2}
.brand{display:flex;align-items:center;gap:3px;font-size:4.6px;font-weight:500;letter-spacing:.3px;line-height:1.05;text-transform:uppercase;color:var(--white)}
.brand-dot{width:11px;height:11px;border-radius:50%;background:var(--white);flex:none}
.nav-links{display:flex;gap:7px;margin-left:auto;margin-right:22px;font-size:2.8px;letter-spacing:.2px;text-transform:uppercase;align-items:center}
.nav-login{border:.6px solid var(--white);padding:2px 8px}
.nav-login--pill{border-radius:5px}
/* shared type */
.eyebrow{font-size:3.2px;letter-spacing:.8px;text-transform:uppercase}
.h-wide{font-weight:500;letter-spacing:.8px;text-transform:uppercase;line-height:1.1}
.p{font-size:3.3px;line-height:1.75;color:var(--body)}
.btn{position:absolute;font-size:2.9px;font-weight:600;letter-spacing:.4px;text-transform:uppercase;display:flex;align-items:center;justify-content:center}
.play{position:absolute;border-radius:50%;background:var(--white);display:flex;align-items:center;justify-content:center}
.play svg{display:block}
.rule{position:absolute;height:.8px;background:var(--ink)}
.input{position:absolute;background:var(--white);border:.5px solid var(--line);font-size:2.6px;color:var(--muted);padding-left:4px;display:flex;align-items:center}
.tile-label{position:absolute;left:5px;bottom:5px;font-size:3px;font-weight:600;letter-spacing:.3px;color:var(--white);text-transform:uppercase;line-height:1.3}
.stat-num{font-size:8px;font-weight:500}
.stat-lbl{font-size:2.8px;text-transform:uppercase;letter-spacing:.2px;margin-top:1px}
/* footer */
.foot-col{position:absolute;font-size:2.7px;line-height:2.6;color:var(--body)}
.foot-title{font-size:3px;font-weight:600;letter-spacing:.3px;text-transform:uppercase;color:var(--ink);margin-bottom:3px;line-height:1}
.foot-row{display:flex;align-items:flex-start;gap:4px;line-height:1.4;margin-bottom:4px}
.foot-ico{width:6px;height:6px;border-radius:50%;flex:none;display:flex;align-items:center;justify-content:center}
.socials{display:flex;gap:2px;margin-top:2px}
.socials span{width:5px;height:5px;border-radius:50%;border:.6px solid currentColor;display:block}
.copy{position:absolute;left:0;right:0;bottom:0;height:15px;border-top:.5px solid var(--line);font-size:2.4px;color:var(--muted);display:flex;align-items:center;justify-content:space-between;padding:0 32px}
.field-line{position:absolute;border-bottom:.5px solid rgba(255,255,255,.55);font-size:2.6px;color:rgba(255,255,255,.75);padding-bottom:2px}
.field-box{position:absolute;border:.5px solid rgba(255,255,255,.5);font-size:2.4px;color:rgba(255,255,255,.8);padding:2px 4px}
</style>
</head>
<body>

<!-- ================= CONCEPT 1 : GREEN ================= -->
<div class="page page--green" style="height:1113px">
  <header style="height:174px">
    <div class="img" role="img" aria-label="Snow-capped mountain range at dusk under a blue sky" style="inset:0;background:linear-gradient(180deg,#2352c9 0%,#3c5fb0 30%,#7a6f9c 48%,#3a4a78 62%,#18233f 100%)"></div>
    <nav class="nav">
      <div class="brand"><span class="brand-dot"></span><span>Veyra<br>Real Estate</span></div>
      <div class="nav-links"><span>About us ▾</span><span>Our businesses ▾</span><span>Investors lobby</span><span>News</span><span>Contact us</span><span class="nav-login">Log in</span></div>
    </nav>
    <div class="abs eyebrow" style="left:26px;top:60px;color:#fff;font-size:3px">Veyra Real Estate</div>
    <div class="abs h-wide" style="left:26px;top:67px;color:#fff;font-size:9.5px;width:150px">Leading global private equity real estate</div>
    <div class="btn" style="left:28px;top:104px;width:38px;height:9px;border:.6px solid #fff;color:#fff">About us</div>
    <div class="play" style="left:194px;top:68px;width:22px;height:22px"><svg width="8" height="9" viewBox="0 0 8 9"><path d="M0 0L8 4.5 0 9z" fill="#1d2b45"/></svg></div>
    <div class="abs" style="left:0;right:0;top:155px;text-align:center;color:#fff;font-size:2.6px;letter-spacing:.6px">SCROLL DOWN<br><svg width="6" height="4" viewBox="0 0 6 4"><path d="M.5.5L3 3 5.5.5" stroke="#fff" fill="none" stroke-width=".7"/></svg></div>
  </header>

  <section style="height:154px">
    <div class="abs eyebrow" style="left:0;right:0;top:32px;text-align:center;color:var(--green)">Who we are</div>
    <div class="abs h-wide" style="left:0;right:0;top:37px;text-align:center;font-size:8px">Veyra Real Estate</div>
    <p class="abs p" style="left:44px;right:44px;top:54px;text-align:center">Lorem ipsum dolor sit amet, consectetur adipiscing elit, sed do eiusmod tempor incididunt ut labore et doloreUt enim ad minim veniam, quis nostrud exercitation ullamcoea Lorem ipsum dolor sit amet, consectetur adipiscingLorem ipsum dolor sit.</p>
    <div class="abs" style="left:34px;right:30px;top:93px;display:flex;justify-content:space-between">
      <div><div class="stat-num">$250</div><div class="stat-lbl">Real estate projects</div></div>
      <div style="border-left:.5px solid var(--line);padding-left:8px"><div class="stat-num">$25B</div><div class="stat-lbl">Private equity</div></div>
      <div style="border-left:.5px solid var(--line);padding-left:8px"><div class="stat-num">$13B</div><div class="stat-lbl">Fund solutions</div></div>
      <div style="border-left:.5px solid var(--line);padding-left:8px"><div class="stat-num">$120B</div><div class="stat-lbl">Credit &amp; insurance</div></div>
    </div>
    <div class="abs" style="left:150px;top:140px;width:.6px;height:14px;background:var(--muted)"></div>
  </section>

  <section style="height:189px;background:linear-gradient(180deg,var(--green) 0%,#2b7f68 100%)">
    <div class="abs eyebrow" style="left:0;right:0;top:15px;text-align:center;color:#fff;font-size:2.7px">Services platform</div>
    <div class="abs h-wide" style="left:0;right:0;top:20px;text-align:center;color:#fff;font-size:8px">Our investment<br>platforms</div>
    <div class="img" role="img" aria-label="Glass office towers seen from below" style="left:30px;top:48px;width:79px;height:55px;background:linear-gradient(160deg,#c9d6e4,#5d7590 60%,#2d3c52)"><div class="tile-label" style="left:10px">Lorem ipsum dolor sit</div></div>
    <div class="abs" style="left:112px;top:48px;width:78px;height:55px;background:#173f5e;border:1.2px solid #2e6a85;color:#fff;text-align:center">
      <div style="font-size:2.7px;margin-top:14px;letter-spacing:.3px">SED PERSPICIATI</div>
      <div style="font-size:3.4px;font-weight:600;letter-spacing:.3px">LOREM IPSUM DOLOR SIT</div>
      <div style="font-size:2.4px;line-height:1.3;padding:1px 10px;opacity:.85">Lorem ipsum dolor sit amet, consectetur adipiscing elit sed do eiusmod tempor</div>
      <div style="margin:2px auto 0;width:26px;border:.5px solid #fff;font-size:2.3px;padding:1px 0">LEARN MORE</div>
    </div>
    <div class="img" role="img" aria-label="Dark glass skyscrapers against a grey sky" style="left:193px;top:48px;width:79px;height:55px;background:linear-gradient(200deg,#e8eef5,#6d7f97 55%,#1f2a3a)"><div class="tile-label" style="left:10px">Lorem ipsum dolor sit</div></div>
    <div class="img" role="img" aria-label="City tower lit in pink at night" style="left:70px;top:107px;width:79px;height:56px;background:linear-gradient(160deg,#3b1f3f,#8a3b6a 45%,#1a1830)"><div class="tile-label" style="left:8px">Lorem ipsum dolor sit</div></div>
    <div class="img" role="img" aria-label="Glass skyscraper under a cloudy sky" style="left:152px;top:107px;width:79px;height:56px;background:linear-gradient(200deg,#f3f6fa,#9bb1c9 50%,#3f5878)"><div class="tile-label" style="left:8px">Lorem ipsum dolor sit</div></div>
  </section>

  <section style="height:135px">
    <div class="img" role="img" aria-label="Twin glass skyscrapers seen from street level" style="left:0;top:0;width:153px;height:135px;border-radius:0 100% 100% 0/0 60% 60% 0;background:linear-gradient(150deg,#e9ecef,#8f969e 45%,#2f3439)"></div>
    <svg class="abs" style="left:100px;top:0" width="60" height="135" viewBox="0 0 60 135"><path d="M0 2 Q56 20 56 68 Q56 118 20 135" fill="none" stroke="#2b4a66" stroke-width=".8"/></svg>
    <div class="abs h-wide" style="left:170px;top:30px;font-size:7.5px">Our edge</div>
    <div class="rule" style="left:170px;top:40px;width:9px"></div>
    <p class="abs p" style="left:170px;top:46px;width:112px;font-size:3px">Lorem ipsum dolor sit amet, consectetur adipiscing elit, sed do eiusmod tempor incididunt ut co laboris nisi ut aliquip ex ea commodo consequat.<br><br>Aabor et dolore magna aliqua. Ut enim ad minim veniam, quis nostrud exercitation ullamco laboris et dolore</p>
    <div class="btn" style="left:171px;top:91px;width:65px;height:12px;background:var(--green);color:#fff">Investor information</div>
  </section>

  <section style="height:97px;background:linear-gradient(180deg,#f3f3f3,#dedede)">
    <div class="img" role="img" aria-label="Faded city skyline" style="left:0;right:0;bottom:0;height:55px;background:linear-gradient(180deg,rgba(200,200,200,0),rgba(180,180,180,.6))"></div>
    <div class="abs h-wide" style="left:0;right:0;top:27px;text-align:center;font-size:7.5px">Stay updated</div>
    <div class="abs" style="left:0;right:0;top:39px;text-align:center;font-size:3.2px;color:var(--body)">Get our latest insights, firm announcements and Charitable Foundation updates.</div>
    <div class="input" style="left:51px;top:52px;width:76px;height:12px">NAME*</div>
    <div class="input" style="left:130px;top:52px;width:76px;height:12px">EMAIL*</div>
    <div class="btn" style="left:208px;top:52px;width:50px;height:12px;background:var(--green);color:#fff;font-size:3.3px">Subscribe</div>
  </section>

  <section style="height:142px">
    <div class="abs h-wide" style="left:30px;top:28px;font-size:7px">Our responsibility</div>
    <div class="rule" style="left:30px;top:38px;width:9px"></div>
    <p class="abs p" style="left:30px;top:44px;width:113px;font-size:3px">Lorem ipsum dolor sit amet, consectetur adipiscing elit, sed do eiusmod tempor incididunt ut co laboris nisi ut aliquip ex ea commodo consequat.<br><br>Aabor et dolore magna aliqua. Ut enim ad minim veniam, quis nostrud exercitation ullamco laboris et dolore</p>
    <div class="btn" style="left:29px;top:91px;width:65px;height:12px;background:var(--green);color:#fff">Investor information</div>
    <div class="abs" style="left:159px;top:28px;width:119px;height:86px;border:.6px solid var(--ink)"></div>
    <div class="img" role="img" aria-label="Colleagues working together at a laptop in a bright office" style="left:154px;top:23px;width:119px;height:87px;background:linear-gradient(135deg,#d9dde2,#8b96a3 50%,#4a5560)"></div>
  </section>

  <section style="height:131px;background:linear-gradient(180deg,#2d9a7e,#3aa689)">
    <div class="abs eyebrow" style="left:32px;top:31px;color:#fff;font-size:2.7px">Contact us</div>
    <div class="abs h-wide" style="left:32px;top:36px;color:#fff;font-size:7.5px">Get in touch<br>with us</div>
    <div class="field-line" style="left:124px;top:31px;width:68px">⚲ First Name</div>
    <div class="field-line" style="left:198px;top:31px;width:64px">⚲ Last Name</div>
    <div class="field-line" style="left:124px;top:44px;width:68px">☏ Phone Number</div>
    <div class="field-line" style="left:198px;top:44px;width:64px">✉ Email address</div>
    <div class="field-line" style="left:124px;top:60px;width:138px;height:20px">Message</div>
    <div class="btn" style="left:125px;top:87px;width:52px;height:12px;border:.6px solid #fff;color:#fff">Submit message</div>
  </section>

  <footer style="height:91px">
    <div class="foot-col" style="left:33px;top:16px"><div class="foot-title">Important links</div>About Us<br>Our Businesses<br>Investor Lobby<br>News<br>Contact Us</div>
    <div class="foot-col" style="left:95px;top:16px;border-left:.5px solid var(--line);padding-left:6px;height:48px"><div class="foot-title">Explore Veyra Real Estate</div>
      <div style="display:flex;gap:16px"><div>Private Equity<br>Real Estate<br>Credit<br>Strategic Partners<br>Tactical Opportunities<br>Infrastructure</div><div>Insurance Solutions<br>Life Sciences<br>Portfolio Operations<br>Technology and Innovations<br>Registered Products</div></div></div>
    <div class="foot-col" style="left:202px;top:16px;border-left:.5px solid var(--line);padding-left:10px;height:48px"><div class="foot-title">Contact details</div>
      <div class="foot-row"><span class="foot-ico" style="background:var(--ink)"></span><span>48 Harbor Row Suite B<br>Palm Cove, FL 33970</span></div>
      <div class="foot-row"><span class="foot-ico" style="background:var(--ink)"></span><span style="font-weight:600">555-014-2207</span></div>
      <div class="foot-row"><span class="foot-ico" style="background:var(--ink)"></span><span>info@veyrarealestate.com</span></div>
      <div class="socials" style="color:var(--ink)"><span></span><span></span><span></span><span></span></div></div>
    <div class="copy" style="height:17px"><span>Copyright © 2022 Veyra Realestate</span><span>Terms of Use &nbsp;|&nbsp; Sitemap &nbsp;|&nbsp; Privacy Policy</span></div>
  </footer>
</div>

<!-- ================= CONCEPT 2 : PURPLE ================= -->
<div class="page page--purple" style="height:1055px">
  <header style="height:187px">
    <div class="img" role="img" aria-label="Aerial view of high-rise apartment towers at night" style="inset:0;background:linear-gradient(180deg,#3b3e4a 0%,#4d4a52 35%,#2a2a33 60%,#16161d 100%)"></div>
    <nav class="nav" style="padding-left:27px">
      <div class="brand"><span class="brand-dot"></span><span>Veyra<br>Real Estate</span></div>
      <div class="nav-links" style="margin-right:22px"><span>About us ▾</span><span>Our businesses ▾</span><span>Investors lobby</span><span>News</span><span>Contact us</span><span class="nav-login nav-login--pill">Log in</span></div>
    </nav>
    <div class="play" style="left:154px;top:67px;width:11px;height:11px;background:none;border:.7px solid #fff"><svg width="4" height="5" viewBox="0 0 8 9"><path d="M0 0L8 4.5 0 9z" fill="#fff"/></svg></div>
    <div class="abs h-wide" style="left:0;right:0;top:84px;text-align:center;color:#fff;font-size:10px;letter-spacing:1px">Leading global private<br>equity real estate</div>
    <div class="btn" style="left:137px;top:112px;width:49px;height:11px;border:.6px solid #fff;color:#fff;font-weight:500">About us</div>
  </header>

  <section style="height:129px;background:var(--grey-band)">
    <div class="abs eyebrow" style="left:36px;top:24px;color:var(--purple-light);font-size:3px">Who we are</div>
    <div class="abs h-wide" style="left:36px;top:30px;font-size:8px">About Veyra<br>real estate</div>
    <p class="abs p" style="left:36px;top:59px;width:120px;font-size:3px">Lorem ipsum dolor sit amet, consectetur adipiscing elit, sed do eiusmod tempor incididunt ut labore et dolore<br><br>Ut enim ad minim veniam, quis nostrud exercitation ullamco laboris nisi ut aliquip ex ea commodo consequat. Duis aute irure dolor in reprehenderi</p>
    <div class="abs" style="left:200px;top:20px;width:65px">
      <div class="stat-num" style="color:var(--purple-light)">$250</div><div class="stat-lbl" style="text-transform:uppercase">Real estate projects</div>
      <div style="border-top:.5px solid #cfcfcf;margin:8px 0"></div>
      <div class="stat-num" style="color:var(--purple-light)">$25B</div><div class="stat-lbl">Private equity</div>
      <div style="border-top:.5px solid #cfcfcf;margin:8px 0"></div>
      <div class="stat-num" style="color:var(--purple-light)">$13B</div><div class="stat-lbl">Fund solutions</div>
    </div>
  </section>

  <section style="height:116px">
    <div class="abs eyebrow" style="left:0;right:0;top:13px;text-align:center;color:var(--purple-light);font-size:2.8px">What we do</div>
    <div class="abs h-wide" style="left:0;right:0;top:18px;text-align:center;font-size:7.5px">Our investment platforms</div>
    <div class="rule" style="left:154px;top:28px;width:10px"></div>
    <div class="img" role="img" aria-label="Hand touching a digital private equity interface" style="left:0;top:40px;width:62px;height:76px;background:linear-gradient(160deg,#9aa0a6,#555b62 55%,#2a2e33)"><div class="tile-label">Sed ut perspiciatis<br>unde omnis</div></div>
    <div class="abs" style="left:63px;top:40px;width:64px;height:76px;background:var(--purple-light);color:#fff;padding:20px 8px 0">
      <div style="font-size:2.8px;font-weight:600;letter-spacing:.3px">SED UT PERSPICIATIS<br>UNDE OMNIS</div>
      <div style="font-size:2.3px;line-height:1.35;margin-top:2px;opacity:.85">Lorem ipsum dolor sit amet, consectetur adipiscing elit, sed do eiusmod tempor incididunt ut labore et</div>
      <div style="margin-top:4px;width:33px;border:.5px solid #fff;border-radius:4px;font-size:2.2px;text-align:center;padding:1px 0">LEARN MORE</div>
    </div>
    <div class="img" role="img" aria-label="Modern office building in black and white" style="left:128px;top:40px;width:63px;height:76px;background:linear-gradient(180deg,#b8bcc0,#6b7075 50%,#2e3236)"><div class="tile-label">Vatem quia voluptas<br>sit aspernatur</div></div>
    <div class="img" role="img" aria-label="Businessman looking over a city skyline" style="left:192px;top:40px;width:64px;height:76px;background:linear-gradient(180deg,#c4c7ca,#7a7f84 50%,#3a3e42)"><div class="tile-label">Sed ut perspiciatis<br>unde omnis</div></div>
    <div class="img" role="img" aria-label="Hazy city skyline" style="left:257px;top:40px;width:61px;height:76px;background:linear-gradient(180deg,#d6d8da,#8d9196 55%,#4a4e52)"><div class="tile-label">Nemo enim ipsam<br>voluptatem</div></div>
  </section>

  <section style="height:143px">
    <div class="abs h-wide" style="left:30px;top:30px;font-size:7.5px">Our edge</div>
    <div class="rule" style="left:30px;top:40px;width:9px"></div>
    <p class="abs p" style="left:30px;top:46px;width:120px;font-size:3px">Lorem ipsum dolor sit amet, consectetur adipiscing elit, sed do eiusmod tempor incididunt ut co laboris nisi ut aliquip ex ea commodo consequat. Duis aute irure dolor in reprehende<br><br>Aabor et dolore magna aliqua. Ut enim ad minim veniam, quis nostrud exercitation ullamco laboris nisi ut aliquip ex ea commodo consequat. Duis aute irure dolor in reprehenderitd exercitation</p>
    <div class="btn" style="left:30px;top:101px;width:72px;height:14px;background:var(--cyan);color:#fff">Investor information</div>
    <div class="img" role="img" aria-label="Twin glass skyscrapers in black and white" style="left:136px;top:0;width:182px;height:143px;clip-path:polygon(100% 0,100% 100%,0 100%);background:linear-gradient(200deg,#f2f2f2,#9a9a9a 45%,#2a2a2a)"></div>
  </section>

  <section style="height:102px;background:linear-gradient(180deg,#ececec,#e2e2e2)">
    <div class="abs h-wide" style="left:0;right:0;top:30px;text-align:center;font-size:7.5px">Stay updated</div>
    <div class="abs" style="left:0;right:0;top:42px;text-align:center;font-size:3.2px;color:var(--body)">Get our latest insights, firm announcements and Charitable Foundation updates.</div>
    <div class="input" style="left:51px;top:55px;width:82px;height:13px">NAME*</div>
    <div class="input" style="left:135px;top:55px;width:81px;height:13px">EMAIL*</div>
    <div class="btn" style="left:218px;top:55px;width:52px;height:13px;background:var(--purple-light);color:#fff;font-size:3.4px">Subscribe</div>
  </section>

  <section style="height:138px">
    <div class="img" role="img" aria-label="Colleagues working together around a laptop, black and white" style="left:0;top:0;width:190px;height:138px;clip-path:polygon(0 0,100% 0,66% 100%,0 100%);background:linear-gradient(135deg,#d4d4d4,#8c8c8c 50%,#3e3e3e)"></div>
    <div class="abs h-wide" style="left:183px;top:28px;font-size:7px">Our responsibility</div>
    <div class="rule" style="left:183px;top:38px;width:9px"></div>
    <p class="abs p" style="left:183px;top:44px;width:112px;font-size:3px">Lorem ipsum dolor sit amet, consectetur adipiscing elit, sed do eiusmod tempor incididunt ut<br><br>Aabor et dolore magna aliqua. Ut enim ad minim veniam, quis nostrud exercitation ullamco laboris nisi ut aliquip ex ea commodo consequat. Duis aute irure dolor in reprehenderitd exercitationna aliqua. Ut enim ad minim veniam.</p>
    <div class="btn" style="left:185px;top:92px;width:44px;height:11px;border:.6px solid var(--teal);color:var(--teal)">Learn more</div>
  </section>

  <section style="height:137px;background:linear-gradient(120deg,#5b2f8c,#6f44a3 60%,#8460b4)">
    <div class="abs" style="left:182px;top:12px;width:110px;height:110px;border-radius:50%;background:rgba(255,255,255,.08)"></div>
    <div class="abs eyebrow" style="left:32px;top:26px;color:#fff;font-size:2.7px">Contact us</div>
    <div class="abs h-wide" style="left:32px;top:30px;color:#fff;font-size:7.5px">Get in touch</div>
    <div class="field-box" style="left:32px;top:46px;width:63px;height:9px">First Name</div>
    <div class="field-box" style="left:96px;top:46px;width:64px;height:9px">Last Name</div>
    <div class="field-box" style="left:32px;top:58px;width:63px;height:9px">Phone Number</div>
    <div class="field-box" style="left:96px;top:58px;width:64px;height:9px">Email address</div>
    <div class="field-box" style="left:32px;top:70px;width:128px;height:20px">Message</div>
    <div class="btn" style="left:32px;top:96px;width:55px;height:11px;border:.6px solid #fff;color:#fff">Submit message</div>
  </section>

  <footer style="height:102px">
    <div class="foot-col" style="left:32px;top:16px"><div class="foot-title">Important links</div>About Us<br>Our Businesses<br>Investor Lobby<br>News<br>Contact Us</div>
    <div class="foot-col" style="left:80px;top:16px;border-left:.5px solid var(--line);padding-left:12px;height:56px"><div class="foot-title">Explore Veyra Real Estate</div>
      <div style="display:flex;gap:16px"><div>Private Equity<br>Real Estate<br>Credit<br>Strategic Partners<br>Tactical Opportunities<br>Infrastructure</div><div>Insurance Solutions<br>Life Sciences<br>Portfolio Operations<br>Technology and Innovations<br>Registered Products</div></div></div>
    <div class="foot-col" style="left:206px;top:16px;border-left:.5px solid var(--line);padding-left:10px;height:56px"><div class="foot-title">Contact details</div>
      <div class="foot-row"><span class="foot-ico" style="background:var(--purple)"></span><span>48 Harbor Row Suite B<br>Palm Cove, FL 33970</span></div>
      <div class="foot-row"><span class="foot-ico" style="background:var(--purple)"></span><span style="font-weight:600">555-014-2207</span></div>
      <div class="foot-row"><span class="foot-ico" style="background:var(--purple)"></span><span style="color:var(--purple)">info@veyrarealestate.com</span></div>
      <div class="socials" style="color:var(--purple)"><span></span><span></span><span></span><span></span></div></div>
    <div class="copy" style="bottom:0;height:20px;padding:0 30px"><span>Copyright © 2022 Veyra Realestate</span><span>Terms of Use &nbsp;|&nbsp; Sitemap &nbsp;|&nbsp; Privacy Policy</span></div>
  </footer>
</div>

<!-- ================= CONCEPT 3 : TEAL ================= -->
<div class="page page--teal" style="height:1116px">
  <header style="height:189px">
    <div class="img" role="img" aria-label="Illuminated financial-district skyline at blue hour" style="inset:0;background:linear-gradient(180deg,#2a4f86 0%,#3b6aa0 30%,#2b4a72 60%,#1a2d4a 100%)"></div>
    <nav class="nav" style="padding-left:27px">
      <div class="brand"><span class="brand-dot"></span><span>Veyra<br>Real Estate</span></div>
      <div class="nav-links" style="margin-right:22px"><span>About us ▾</span><span>Our businesses ▾</span><span>Investors lobby</span><span>News</span><span>Contact us</span><span class="nav-login">Log in</span></div>
    </nav>
    <div class="play" style="left:163px;top:58px;width:12px;height:12px;background:none;border:.7px solid #fff"><svg width="4" height="5" viewBox="0 0 8 9"><path d="M0 0L8 4.5 0 9z" fill="#fff"/></svg></div>
    <div class="abs" style="left:0;right:0;top:74px;text-align:center;color:#fff;font-size:13.5px;font-weight:300;line-height:1.05">Leading Global Private<br><b style="font-weight:700">Equity Real Estate</b></div>
    <div class="btn" style="left:136px;top:110px;width:52px;height:12px;background:var(--teal);color:#fff;font-size:3.3px">About us ›</div>
  </header>

  <section style="height:156px;background:linear-gradient(180deg,#f1f3f4 55%,#dfe3e6)">
    <div class="img" role="img" aria-label="Faded city skyline" style="left:0;right:0;bottom:0;height:70px;background:linear-gradient(180deg,rgba(220,224,227,0),rgba(190,197,202,.8))"></div>
    <div class="abs" style="left:0;right:0;top:23px;text-align:center;font-size:9px;text-transform:uppercase;font-weight:300"><b style="font-weight:700">About</b> Veyra Real Estate</div>
    <p class="abs p" style="left:52px;right:52px;top:44px;text-align:center;font-size:3.2px">Lorem ipsum dolor sit amet, consectetur adipiscing elit, sed do eiusmod tempor incididunt ut labore et dolore magna aliqua. Ut enim ad minim veniam, quis nostrud exercitation ullamco laboris nisi ut aliquip ex ea commodo consequat. Duis aute irure dolor in reprehenderit in voluptate ve</p>
    <div class="abs" style="left:37px;top:90px;width:50px;text-align:center"><div class="stat-num" style="color:var(--teal);font-weight:700">$250</div><div class="stat-lbl" style="font-weight:700">Real estate projects</div></div>
    <div class="abs" style="left:101px;top:83px;width:62px;height:35px;background:var(--teal-dark);color:#fff;text-align:center;padding-top:9px"><div class="stat-num" style="font-weight:700">$25B</div><div class="stat-lbl" style="font-weight:700">Private equity</div></div>
    <div class="abs" style="left:172px;top:90px;width:52px;text-align:center"><div class="stat-num" style="color:var(--teal);font-weight:700">$25B</div><div class="stat-lbl" style="font-weight:700">Fund solutions</div></div>
    <div class="abs" style="left:238px;top:90px;width:56px;text-align:center"><div class="stat-num" style="color:var(--teal);font-weight:700">$120B</div><div class="stat-lbl" style="font-weight:700">Credit &amp; insurance</div></div>
  </section>

  <section style="height:120px">
    <div class="abs" style="left:0;right:0;top:17px;text-align:center;font-size:9px;text-transform:uppercase;font-weight:300"><b style="font-weight:700">Our investment</b> platforms</div>
    <div class="abs" style="left:154px;top:30px;width:14px;height:1px;background:var(--teal)"></div>
    <div class="img" role="img" aria-label="Hand touching a digital private equity interface" style="left:0;top:48px;width:64px;height:72px;background:linear-gradient(160deg,#6c8fb0,#3b5776 55%,#1f2f44)"><div class="tile-label" style="left:12px;text-align:center">Sed ut perspiciatis<br>unde omnis</div></div>
    <div class="abs" style="left:64px;top:43px;width:64px;height:77px;background:var(--teal-dark);color:#fff;text-align:center;padding:20px 6px 0">
      <div style="font-size:3px;font-weight:700">SED UT PERSPICIATIS<br>UNDE OMNIS</div>
      <div style="font-size:2.3px;line-height:1.35;margin-top:2px;opacity:.8">Lorem ipsum dolor sit amet, consectetur adipiscing elit, sed do eiusmod tempor incididunt ut labore et</div>
      <div style="margin:4px auto 0;width:34px;border:.5px solid #fff;font-size:2.2px;padding:1.5px 0">LEARN MORE</div>
    </div>
    <div class="img" role="img" aria-label="Modern office building at dusk" style="left:128px;top:48px;width:65px;height:72px;background:linear-gradient(180deg,#8fa4bb,#4d6580 50%,#283c52)"><div class="tile-label" style="left:7px;text-align:center">Vatem quia voluptas<br>sit aspernatur</div></div>
    <div class="img" role="img" aria-label="Businessman looking over a city skyline" style="left:193px;top:48px;width:65px;height:72px;background:linear-gradient(180deg,#7f98b3,#415a76 55%,#1f2e42)"><div class="tile-label" style="left:10px;text-align:center">Sed ut perspiciatis<br>unde omnis</div></div>
    <div class="img" role="img" aria-label="Hazy city skyline at sunset" style="left:258px;top:48px;width:64px;height:72px;background:linear-gradient(180deg,#c9b9a8,#8a8f98 55%,#4a5260)"><div class="tile-label" style="left:9px;text-align:center">Nemo enim ipsam<br>voluptatem</div></div>
  </section>

  <section style="height:173px">
    <div class="abs" style="left:33px;top:44px;font-size:9px;text-transform:uppercase;font-weight:300">Our <b style="font-weight:700">edge</b></div>
    <div class="abs" style="left:33px;top:56px;width:10px;height:1px;background:var(--teal)"></div>
    <p class="abs p" style="left:33px;top:62px;width:115px;font-size:3px">Lorem ipsum dolor sit amet, consectetur adipiscing elit, sed do eiusmod tempor incididunt ut co laboris nisi ut aliquip ex ea commodo consequat. Duis aute irure dolor in reprehende<br><br>Aabor et dolore magna aliqua. Ut enim ad minim veniam, quis nostrud exercitation ullamco laboris nisi ut aliquip ex ea commodo consequat. Duis aute irure dolor in reprehenderitd exercitation.na aliqua. Ut enim ad minim veniam.</p>
    <div class="btn" style="left:33px;top:122px;width:72px;height:14px;border:.7px solid var(--teal);color:var(--teal);font-weight:500">Investor information</div>
    <div class="abs" style="left:166px;top:27px;width:156px;height:124px;border:.6px solid #9fb5b8;border-right:none"></div>
    <div class="img" role="img" aria-label="Blue glass skyscrapers among trees under a clear sky" style="left:170px;top:30px;width:152px;height:122px;background:linear-gradient(200deg,#cfe3f5,#4f86c2 45%,#1f3f6b 80%,#3f6b3a)"></div>
  </section>

  <section style="height:96px;background:linear-gradient(180deg,#e4eeee,#d7e5e4)">
    <div class="abs" style="left:0;right:0;top:20px;text-align:center;font-size:9px;text-transform:uppercase;font-weight:300"><b style="font-weight:700">Stay</b> updated</div>
    <div class="abs" style="left:154px;top:32px;width:14px;height:1px;background:var(--teal)"></div>
    <div class="abs" style="left:0;right:0;top:40px;text-align:center;font-size:3.4px;color:var(--body)">Get our latest insights, firm announcements and Charitable Foundation updates.</div>
    <div class="input" style="left:61px;top:55px;width:76px;height:13px;color:var(--teal)">NAME*</div>
    <div class="input" style="left:139px;top:55px;width:76px;height:13px;color:var(--teal)">EMAIL*</div>
    <div class="btn" style="left:218px;top:55px;width:43px;height:13px;background:var(--teal);color:#fff;font-size:3.1px">Subscribe</div>
  </section>

  <section style="height:140px">
    <div class="img" role="img" aria-label="Colleagues working together around a laptop in a modern office" style="left:0;top:0;width:160px;height:140px;background:linear-gradient(135deg,#d7dee2,#7f8f99 50%,#3c4a54)"></div>
    <div class="abs" style="left:183px;top:29px;font-size:9px;text-transform:uppercase;font-weight:300">Our <b style="font-weight:700">responsibility</b></div>
    <div class="abs" style="left:183px;top:41px;width:10px;height:1px;background:var(--teal)"></div>
    <p class="abs p" style="left:183px;top:47px;width:115px;font-size:3px">Lorem ipsum dolor sit amet, consectetur adipiscing elit, sed do eiusmod tempor incididunt ut<br><br>Aabor et dolore magna aliqua. Ut enim ad minim veniam, quis nostrud exercitation ullamco laboris nisi ut aliquip ex ea commodo consequat. Duis aute irure dolor in reprehenderitd exercitationna aliqua. Ut enim ad minim veniam.</p>
    <div class="btn" style="left:184px;top:95px;width:45px;height:12px;border:.7px solid var(--teal);color:var(--teal);font-weight:500">Learn more</div>
  </section>

  <section style="height:139px;background:var(--teal)">
    <div class="abs" style="left:-30px;top:30px;width:90px;height:90px;border-radius:50%;background:rgba(255,255,255,.06)"></div>
    <div class="abs" style="left:0;right:0;top:20px;text-align:center;font-size:9px;text-transform:uppercase;font-weight:300;color:#fff">Get <b style="font-weight:700">in touch</b></div>
    <div class="abs" style="left:154px;top:32px;width:14px;height:1px;background:#fff"></div>
    <div class="input" style="left:77px;top:43px;width:86px;height:11px;border:none">First Name</div>
    <div class="input" style="left:165px;top:43px;width:86px;height:11px;border:none">Last Name</div>
    <div class="input" style="left:77px;top:56px;width:86px;height:11px;border:none">Phone Number</div>
    <div class="input" style="left:165px;top:56px;width:86px;height:11px;border:none">Email address</div>
    <div class="input" style="left:77px;top:69px;width:174px;height:21px;border:none;align-items:flex-start;padding-top:3px">Message</div>
    <div class="btn" style="left:139px;top:98px;width:55px;height:12px;border:.7px solid #fff;color:#fff">Submit message</div>
  </section>

  <footer style="height:103px">
    <div class="foot-col" style="left:33px;top:16px"><div class="foot-title">Important links</div>About Us<br>Our Businesses<br>Investor Lobby<br>News<br>Contact Us</div>
    <div class="foot-col" style="left:82px;top:0;border-left:.5px solid var(--line);padding:16px 0 0 12px;height:80px"><div class="foot-title">Explore Veyra Real Estate</div>
      <div style="display:flex;gap:16px"><div>Private Equity<br>Real Estate<br>Credit<br>Strategic Partners<br>Tactical Opportunities<br>Infrastructure</div><div>Insurance Solutions<br>Life Sciences<br>Portfolio Operations<br>Technology and Innovations<br>Registered Products</div></div></div>
    <div class="foot-col" style="left:210px;top:0;border-left:.5px solid var(--line);padding:16px 0 0 17px;height:80px"><div class="foot-title">Contact details</div>
      <div class="foot-row"><span class="foot-ico" style="background:var(--teal-dark)"></span><span>48 Harbor Row Suite B<br>Palm Cove, FL 33970</span></div>
      <div class="foot-row"><span class="foot-ico" style="background:var(--teal-dark)"></span><span style="font-weight:600">555-014-2207</span></div>
      <div class="foot-row"><span class="foot-ico" style="background:var(--teal-dark)"></span><span style="color:var(--teal-dark)">info@veyrarealestate.com</span></div>
      <div class="socials" style="color:var(--teal-dark)"><span></span><span></span><span></span><span></span></div></div>
    <div class="copy" style="height:20px"><span>Copyright © 2022 Veyra Realestate</span><span>Terms of Use &nbsp;|&nbsp; Sitemap &nbsp;|&nbsp; Privacy Policy</span></div>
  </footer>
</div>

</body>
</html>
```